Heron Property Inspection business card

I am the principal inspector of Heron Property Inspections. I serve Northern Virginia from Winchester to Arlington.Associate, Federated Guild of Dwelling Examiners (FGDE)Graduate, FGDE Home Inspectors CourseNational Association of Home Inspectors ExamI'd like the business card to look more professional than comical.I pulled the attached picture off the web. I'd like to have something like that or an image of a house as my logo on the cards.

Target Market(s)

Persons who recently purchased a home.

Industry/Entity Type

Business

Contact Information for Business Card

Heron Property Inspections, LLC.4455 River RoadBluemont, Virginia 20135cell: 703-231-6680e-mail: tkmarlow@postvale.net

Font styles to use
Serif
Sans Serif

Requirements
Must have
• I'd like to have a logo, something that identifies me as a home inspector. The attached images are something that I'd like to have incorporated into my business card logo.
Nice to have
• I'd like a sketch of a house and/or a magnifying glass showing a house being inspected. The attached images are used as a suggestion only, I do not own the images.
Should not have
• Gimmicky stuff. I want to appear professional and trustworthy.

```html
<!DOCTYPE html>
<html lang="en">
<head>
<meta charset="utf-8">
<title>Heron Property Inspections – Business Card</title>
<link href="https://fonts.googleapis.com/css2?family=Arimo:wght@400;700&display=swap" rel="stylesheet">
<style>
  :root {
    --page-bg: #d9d5cf;
    --card-black: #0b0b0c;
    --card-sheen: #1e1e21;
    --accent-red: #c1272d;
    --text-white: #f4f4f4;
    --logo-grey: #6d6d70;
  }
  html, body {
    margin: 0;
    width: 1200px;
    height: 892px;
    overflow: hidden;
    background: var(--page-bg);
  }
  .canvas {
    position: relative;
    width: 1200px;
    height: 892px;
    display: flex;
    align-items: center;
    justify-content: center;
  }
  .card {
    position: relative;
    width: 1000px;
    height: 572px;
    border-radius: 34px;
    background:
      linear-gradient(125deg, var(--card-black) 0%, var(--card-sheen) 42%, var(--card-black) 58%, #141416 100%);
    box-shadow: 0 18px 40px rgba(0,0,0,.35);
    font-family: "Arimo", Arial, sans-serif;
    color: var(--text-white);
    overflow: hidden;
  }
  .brand {
    position: absolute;
    top: 66px;
    right: 70px;
    text-align: right;
  }
  .brand-name {
    font-size: 34px;
    font-weight: 700;
    color: var(--logo-grey);
    letter-spacing: .5px;
    line-height: 1.1;
  }
  .brand-rule {
    margin-top: 12px;
    height: 3px;
    background: var(--accent-red);
  }
  .divider {
    position: absolute;
    left: 100px;
    right: 70px;
    top: 262px;
    height: 2px;
    background: var(--accent-red);
  }
  .person {
    position: absolute;
    right: 70px;
    top: 290px;
    text-align: right;
  }
  .person-name {
    font-size: 40px;
    letter-spacing: 1px;
  }
  .name-rule {
    margin: 12px 0 10px auto;
    width: 330px;
    height: 2px;
    background: var(--accent-red);
  }
  .person-role {
    font-size: 22px;
  }
  .address {
    margin-top: 22px;
    font-size: 22px;
    line-height: 1.3;
  }
  .contacts {
    position: absolute;
    left: 100px;
    top: 290px;
    list-style: none;
    margin: 0;
    padding: 0;
  }
  .contact-item {
    display: flex;
    align-items: center;
    gap: 16px;
    font-size: 24px;
    margin-bottom: 10px;
  }
  .contact-icon {
    width: 34px;
    height: 34px;
    flex: none;
  }
</style>
</head>
<body>
<main class="canvas">
  <article class="card">
    <header class="brand">
      <div class="brand-name">Heron Property Inspections, LLC</div>
      <div class="brand-rule"></div>
    </header>

    <div class="divider"></div>

    <ul class="contacts">
      <li class="contact-item">
        <svg class="contact-icon" viewBox="0 0 34 34" aria-hidden="true">
          <rect x="1.5" y="1.5" width="31" height="31" fill="none" stroke="#f4f4f4" stroke-width="2"/>
          <rect x="11" y="6" width="12" height="22" rx="2" fill="var(--accent-red)"/>
          <rect x="13" y="9" width="8" height="7" fill="#0b0b0c"/>
          <rect x="13" y="19" width="8" height="6" fill="#0b0b0c" opacity=".5"/>
        </svg>
        <span>703-555-0192</span>
      </li>
      <li class="contact-item">
        <svg class="contact-icon" viewBox="0 0 34 34" aria-hidden="true">
          <rect x="1.5" y="1.5" width="31" height="31" fill="none" stroke="#f4f4f4" stroke-width="2"/>
          <rect x="6" y="10" width="22" height="15" fill="var(--accent-red)"/>
          <path d="M6 10 L17 19 L28 10 M6 25 L14 17 M28 25 L20 17" fill="none" stroke="#0b0b0c" stroke-width="1.6"/>
        </svg>
        <span>tkmarlow@postvale.net</span>
      </li>
    </ul>

    <section class="person">
      <div class="person-name">Employee Name</div>
      <div class="name-rule"></div>
      <div class="person-role">Your Position</div>
      <address class="address" style="font-style:normal">
        7182 Quarry Lane<br>Fernhill, Virginia 20148
      </address>
    </section>
  </article>
</main>
</body>
</html>
```